Pipe Repair Clamps

A double side A4 showing our pipe repair clamps for stopping leaking pipes within seconds. For water , sewage companies, hotels, malls, airports, hosptals, facilities management companies and district cooling companies. Reverse side will show a size chart. Examples of product uploaded

```html
<!DOCTYPE html>
<html lang="en">
<head>
<meta charset="utf-8">
<title>Pipe Repair Clamps</title>
<link rel="stylesheet" href="https://fonts.googleapis.com/css2?family=Anton&family=Roboto:ital,wght@0,500;0,700;0,900;1,900&display=swap">
<style>
:root{
  --navy:#2b2866;
  --aqua:#29abe2;
  --white:#ffffff;
  --steel-dark:#3a3a3a;
  --steel-light:#f2f2f2;
}
*{margin:0;padding:0;box-sizing:border-box}
html,body{width:927px;height:1200px;overflow:hidden;background:var(--white)}
.flyer{position:relative;width:927px;height:1200px;font-family:"Roboto",sans-serif;color:var(--navy)}
.pipe{position:absolute;left:0;top:108px;width:927px;height:56px;
  background:linear-gradient(to bottom,#6d6d6d 0%,var(--steel-light) 35%,#9a9a9a 70%,var(--steel-dark) 100%)}
.logo-box{position:absolute;left:68px;top:50px;width:384px;height:143px;background:var(--navy);
  display:flex;align-items:center;justify-content:center;color:var(--white);font-weight:500;font-size:28px}
.splash{position:absolute;left:644px;top:16px;width:212px;height:284px;border-radius:40%;
  background:radial-gradient(circle,var(--aqua) 0%,rgba(41,171,226,.35) 55%,rgba(255,255,255,0) 75%)}
.drips{position:absolute;left:680px;top:328px;width:136px;height:224px;
  background:linear-gradient(to bottom,rgba(41,171,226,.5),rgba(41,171,226,.25));border-radius:8px}
.headline{position:absolute;left:68px;top:232px;font-family:"Anton",sans-serif;font-size:70px;line-height:1;letter-spacing:.5px}
.tagline{position:absolute;left:68px;top:322px;font-weight:500;line-height:1}
.tagline .line1{display:flex;align-items:baseline;gap:14px}
.tagline .small{font-size:30px}
.tagline .accent{color:var(--aqua);font-weight:900;font-style:italic;font-size:60px}
.tagline .line2{margin-top:12px;font-size:44px}
.tagline .line2 .small{font-size:28px}
.product{position:absolute;top:456px;height:120px;border-radius:6px}
.product-small{left:68px;width:88px;background:linear-gradient(135deg,#5a5a5a,#b9b9b9)}
.product-band{left:196px;width:140px;background:linear-gradient(135deg,#222,#8c8c8c)}
.product-sleeve{left:372px;width:156px;background:linear-gradient(135deg,#2a5fc4,#d8d8d8)}
.sectors{position:absolute;left:0;top:602px;width:927px;height:308px;background:var(--navy);color:var(--white);
  text-align:center;font-weight:500;font-size:33px;line-height:42.5px;padding-top:44px}
.sectors .sep{display:inline-block;margin:0 34px}
.sectors .small{font-size:24px}
.cta{position:absolute;left:0;top:946px;width:927px;height:48px}
.stripes{position:absolute;top:16px;height:28px;
  background:repeating-linear-gradient(to bottom,var(--aqua) 0 4px,transparent 4px 11px)}
.stripes.left{left:0;width:282px}
.stripes.right{left:648px;width:279px}
.cta-text{position:absolute;left:0;width:927px;text-align:center;top:0;font-weight:500;font-size:50px;line-height:48px}
.phone{position:absolute;left:0;width:927px;text-align:center;top:1000px;font-weight:900;font-size:113px;line-height:110px}
.web{position:absolute;left:0;width:927px;text-align:center;top:1116px;font-weight:900;font-size:30px;letter-spacing:9px}
</style>
</head>
<body>
<div class="flyer">
  <div class="pipe"></div>
  <div class="logo-box">YOUR LOGO</div>
  <div class="splash" role="img" aria-label="Illustration of water bursting from a leaking pipe joint"></div>
  <div class="drips" role="img" aria-label="Illustration of water drops falling into a puddle"></div>

  <h1 class="headline">PIPE REPAIR CLAMPS</h1>
  <div class="tagline">
    <div class="line1"><span class="small">FOR</span><span class="accent">STOPPING LEAKING</span></div>
    <div class="line2">PIPES <span class="small">WITHIN</span> SECONDS.</div>
  </div>

  <div class="product product-small" role="img" aria-label="Photo of a small pipe repair clamp with bolts"></div>
  <div class="product product-band" role="img" aria-label="Photo of a rubber-lined band repair clamp"></div>
  <div class="product product-sleeve" role="img" aria-label="Photo of a stainless steel sleeve repair clamp"></div>

  <div class="sectors">
    FOR<br>
    WATER<span class="sep">|</span>SEWAGE COMPANIES<span class="sep">|</span>HOTELS<span class="sep">|</span><br>
    MALLS<span class="sep">|</span>AIRPORTS<span class="sep">|</span>HOSPTALS<span class="sep">|</span><br>
    FACILITIES MANAGEMENT COMPANIES <span class="small">AND</span><br>
    DISTRICT COOLING COMPANIES.
  </div>

  <div class="cta">
    <div class="stripes left"></div>
    <div class="cta-text">CALL US NOW</div>
    <div class="stripes right"></div>
  </div>
  <div class="phone">123 456 7890</div>
  <div class="web">WWW.YOURWEBSITE.COM</div>
</div>
</body>
</html>
```